Business Card & Email Signature Design || Upmarket + Luxury

Rima Vale Honey, a New Zealand Manuka Honey company needs a Business Card & Email Signature design.

Our logo's are attached in Gold & Black versions, feel free to be creative with how you use the logo and it's patterns in your design.

Style:
- Looking for an Elegant, Luxurious, Upmarket feel.
- Black/Matte Black Card, Gold Foil, UV Embossing

Information to Add:

- Logo
- Company Name: Rima Vale Honey
- Name: Martin Holloway
- Title: Creative Director
- Phone: +64 2815 96 417
- Email: martin@rimavalehoney.example.nz
- Website: www.rimavalehoney.example.nz

- Socials: ***For email Signature Only***
- Facebook: https://www.facebook.com/rimavalehoney/
- Instagram: https://www.instagram.com/rimavalehoney/

Target Market(s)

Asia/Europe Luxury, Upmarket

Contact Information for Business Card

- Logo
- Name: Martin Holloway
- Phone: +64 2815 96 417

Font styles to use
Other font styles liked:
• Champagne & Limousines (Attached)

Requirements
Must have
• Business Card & Email Signature Design.

Looking for a Sleek, Luxury, Upmarket Design.

```html
<!DOCTYPE html>
<html lang="en">
<head>
<meta charset="utf-8">
<title>Rima Vale Honey — Business Card &amp; Email Signature</title>
<link rel="stylesheet" href="https://fonts.googleapis.com/css2?family=Arimo:wght@400&family=Lato:wght@400;700&family=Poppins:wght@600&display=swap">
<style>
  :root {
    --board: #434343;
    --card-black: #0d0d0d;
    --card-black-2: #1b1b1b;
    --gold: #c9a45f;
    --gold-icon: #d8b772;
    --ink: #333333;
    --ink-dark: #1a1a1a;
    --social-dot: #2b2b2b;
    --white: #ffffff;
  }
  * { box-sizing: border-box; margin: 0; padding: 0; }
  html, body { width: 1200px; height: 1133px; overflow: hidden; background: var(--board); }
  .board { position: relative; width: 1200px; height: 1133px; }

  .card {
    position: absolute; top: 304px; width: 390px; height: 231px; overflow: hidden;
    background: linear-gradient(160deg, var(--card-black-2), var(--card-black) 60%);
    box-shadow: 3px 3px 4px rgba(0,0,0,.6);
  }
  .card--front { left: 164px; }
  .card--back { left: 595px; }

  .foil-band { position: absolute; inset: 0; width: 100%; height: 100%; }

  .card__seal {
    position: absolute; left: 30px; top: 32px; width: 116px; height: 116px;
    border: 1px solid var(--gold); border-radius: 50%;
    display: flex; align-items: center; justify-content: center; text-align: center;
    font-family: "Lato", sans-serif; font-size: 13px; letter-spacing: 1px;
    color: var(--gold); padding: 0 14px; line-height: 1.3;
  }

  .card__identity { position: absolute; right: 28px; top: 29px; text-align: right; }
  .card__name {
    font-family: "Poppins", sans-serif; font-weight: 600; font-size: 14.5px;
    color: var(--gold); letter-spacing: .3px; line-height: 1;
  }
  .card__title { font-family: "Arimo", sans-serif; font-size: 11px; color: var(--white); margin-top: 3px; }

  .card__contacts {
    position: absolute; right: 27px; top: 78px; list-style: none;
    font-family: "Arimo", sans-serif; font-size: 10.5px; color: var(--white); text-align: right;
  }
  .card__contacts li { display: flex; align-items: center; justify-content: flex-end; gap: 5px; height: 14px; white-space: nowrap; }
  .card__contacts svg { width: 12px; height: 12px; }

  .card__web {
    position: absolute; right: 27px; top: 196px;
    font-family: "Arimo", sans-serif; font-size: 10.5px; color: var(--ink-dark); white-space: nowrap;
  }

  .card__brand {
    position: absolute; left: 0; right: 0; top: 138px; text-align: center; white-space: nowrap;
    font-family: "Lato", sans-serif; font-weight: 400; font-size: 26px;
    letter-spacing: 5px; color: var(--gold);
  }

  .signature {
    position: absolute; left: 159px; top: 630px; width: 822px; height: 247px;
    background: var(--white); overflow: hidden;
  }
  .signature__name {
    position: absolute; left: 40px; top: 22px;
    font-family: "Lato", sans-serif; font-weight: 700; font-size: 31px; color: var(--gold); line-height: 1;
  }
  .signature__title {
    position: absolute; left: 40px; top: 57px;
    font-family: "Lato", sans-serif; font-size: 20px; color: var(--ink);
  }
  .signature__contacts {
    position: absolute; left: 40px; top: 97px; list-style: none;
    font-family: "Lato", sans-serif; font-size: 20px; color: var(--ink);
  }
  .signature__contacts li { display: flex; align-items: center; gap: 9px; height: 25px; white-space: nowrap; }
  .signature__contacts svg { width: 22px; height: 22px; }
  .signature__brand {
    position: absolute; left: 420px; width: 370px; top: 46px; text-align: center; white-space: nowrap;
    font-family: "Lato", sans-serif; font-size: 25px; letter-spacing: 5px; color: var(--gold);
  }
  .signature__social {
    position: absolute; left: 468px; top: 194px; display: flex; align-items: center; gap: 5px; white-space: nowrap;
    font-family: "Lato", sans-serif; font-size: 19px; color: var(--ink);
  }
  .signature__social-dot { width: 26px; height: 26px; border-radius: 50%; background: var(--social-dot); }
  .signature__social-label { margin-right: 6px; }
  .signature__handle { margin-left: 8px; }
</style>
</head>
<body>
<main class="board">

  <section class="card card--front" aria-label="Business card front">
    <svg class="foil-band" viewBox="0 0 390 231" preserveAspectRatio="none" role="img" aria-label="Gold foil band along the lower edge">
      <defs>
        <linearGradient id="goldCard" x1="0" y1="0" x2="1" y2="0.3">
          <stop offset="0" stop-color="#c9a063"/>
          <stop offset="0.55" stop-color="#ead9a0"/>
          <stop offset="1" stop-color="#c29a5c"/>
        </linearGradient>
      </defs>
      <path d="M0 186 C90 212 200 196 280 160 C320 144 360 140 390 148 L390 231 L0 231 Z" fill="url(#goldCard)"/>
    </svg>
    <div class="card__seal">Rima Vale Honey</div>
    <div class="card__identity">
      <p class="card__name">MARTIN HOLLOWAY</p>
      <p class="card__title">Creative Director</p>
    </div>
    <ul class="card__contacts">
      <li>+64 2815 96 417
        <svg viewBox="0 0 24 24" aria-hidden="true"><path d="M6 3l4 4-2 3c1 2 4 5 6 6l3-2 4 4-3 3C10 21 3 14 3 6z" fill="none" stroke="#d8b772" stroke-width="2"/></svg>
      </li>
      <li>martin@rimavalehoney.example.nz
        <svg viewBox="0 0 24 24" aria-hidden="true"><rect x="2" y="5" width="20" height="14" fill="#d8b772"/><polyline points="2,5 12,13 22,5" fill="none" stroke="#111" stroke-width="1.5"/></svg>
      </li>
    </ul>
    <p class="card__web">www.rimavalehoney.example.nz</p>
  </section>

  <section class="card card--back" aria-label="Business card back">
    <p class="card__brand">RIMA VALE HONEY</p>
  </section>

  <section class="signature" aria-label="Email signature">
    <svg class="foil-band" viewBox="0 0 822 247" preserveAspectRatio="none" role="img" aria-label="Gold foil band along the lower edge">
      <defs>
        <linearGradient id="goldSig" x1="0" y1="0" x2="1" y2="0.2">
          <stop offset="0" stop-color="#c9a063"/>
          <stop offset="0.5" stop-color="#ead9a0"/>
          <stop offset="1" stop-color="#c29a5c"/>
        </linearGradient>
      </defs>
      <path d="M0 192 C150 236 320 226 480 186 C620 152 720 150 822 190 L822 247 L0 247 Z" fill="url(#goldSig)"/>
    </svg>
    <p class="signature__name">Martin Holloway</p>
    <p class="signature__title">Creative Director</p>
    <ul class="signature__contacts">
      <li><svg viewBox="0 0 24 24" aria-hidden="true"><path d="M6 3l4 4-2 3c1 2 4 5 6 6l3-2 4 4-3 3C10 21 3 14 3 6z" fill="none" stroke="#d8b772" stroke-width="2"/></svg>+64 2815 96 417</li>
      <li><svg viewBox="0 0 24 24" aria-hidden="true"><rect x="2" y="5" width="20" height="14" fill="#e3c77e"/><polyline points="2,5 12,13 22,5" fill="none" stroke="#fff" stroke-width="1.5"/></svg>martin@rimavalehoney.example.nz</li>
      <li><svg viewBox="0 0 24 24" aria-hidden="true"><g fill="none" stroke="#e3c77e" stroke-width="1.6"><circle cx="12" cy="12" r="9"/><ellipse cx="12" cy="12" rx="4" ry="9"/><line x1="3" y1="12" x2="21" y2="12"/><line x1="5" y1="7" x2="19" y2="7"/><line x1="5" y1="17" x2="19" y2="17"/></g></svg>www.rimavalehoney.example.nz</li>
    </ul>
    <p class="signature__brand">RIMA VALE HONEY</p>
    <div class="signature__social">
      <span class="signature__social-label">Follow us on:</span>
      <span class="signature__social-dot" aria-hidden="true"></span>
      <span class="signature__social-dot" aria-hidden="true"></span>
      <span class="signature__handle">/ &nbsp;rimavalehoney</span>
    </div>
  </section>

</main>
</body>
</html>
```